Business Cards for new orthopaedic surgery practice

My husband and I are starting our own orthopaedic surgery practice. We are looking for a business card that is uniform, but one will have my name/title and the other will have his. You can just create one design with my name on it for now. But when I choose your design as the winning design I will ask that you add another copy with his name/title.

We are looking for classy, simple, elite all in one. We like dark blues/a little gold/yellow. Something that goes with our logo. We want our logo incorporated. Here is all the info you need:
Business name: RV Bone & Vitality Center
Location: 38517 North Willowmere Ave
Palm Haven, FL 33490
Phone: 954-218-4063
Fax: 954-582-7341
Email: info@myrvbonecare.example

Names: Lydia Vance, M.D.
Board Certified Hand and Upper Extremity Surgeon

Ebo Dansu, M.D.
Board Certified Hip & Knee Replacement/General Orthopaedic Surgeon

Can decide what you want to put on the back. Maybe a slogan:
Steady Hands. Lasting Strength

I am just going to upload our logo. The only thing is if we select you as the winning design, the location, and phone numbers may change. We will need your help to update that once fully solidified.

Industry/Entity Type

Medical

Contact Information for Business Card

Colors
0054AA
0677BA
7BADD7
CADEEF
E8F1F8
0094D4
00A9DD
6FCCEA
C7EBF8
E9F6FB

Requirements
Must have
• class, appeal,
Should not have
• We want to air on the side of masculine if we are looking at masculine vs. feminine feel. But we still want it classy, sophisticated, and something we will love

```html
<!DOCTYPE html>
<html lang="en">
<head>
<meta charset="utf-8">
<title>RV Bone &amp; Vitality Center — Business Cards</title>
<link href="https://fonts.googleapis.com/css2?family=Libre+Baskerville:wght@400;700&family=Montserrat:wght@400;500&display=swap" rel="stylesheet">
<style>
  :root {
    --navy: #1b2a52;
    --gold: #c9a55c;
    --white: #ffffff;
    --stage: #2b2b2d;
  }
  * { box-sizing: border-box; margin: 0; padding: 0; }
  html, body { width: 1200px; height: 875px; overflow: hidden; }
  body {
    background: var(--stage);
    font-family: "Montserrat", sans-serif;
    position: relative;
  }
  .card {
    position: absolute;
    width: 540px;
    height: 310px;
    background: var(--navy);
    border-radius: 18px;
    overflow: hidden;
    color: var(--white);
  }
  .card--back { left: 40px; top: 282px; }
  .card--front { left: 620px; top: 282px; }

  .brand {
    position: absolute;
    display: flex;
    align-items: center;
    justify-content: center;
    text-align: center;
    border: 2px solid var(--gold);
    border-radius: 50%;
    font-family: "Libre Baskerville", serif;
    font-weight: 400;
    color: var(--white);
    letter-spacing: 0.12em;
    text-transform: uppercase;
    line-height: 1.5;
  }
  .card--back .brand {
    width: 150px; height: 150px;
    left: 195px; top: 48px;
    font-size: 13px;
  }
  .card--front .brand {
    width: 132px; height: 132px;
    left: 362px; top: 28px;
    font-size: 11.5px;
    z-index: 2;
  }
  .tagline {
    position: absolute;
    left: 0; right: 0; top: 236px;
    text-align: center;
    font-size: 14px;
    letter-spacing: 0.02em;
  }

  .swoosh { position: absolute; inset: 0; width: 540px; height: 310px; }

  .identity {
    position: absolute;
    left: 0; top: 52px;
    padding-left: 52px;
  }
  .identity::before {
    content: "";
    position: absolute;
    left: 22px; top: 2px;
    width: 18px; height: 52px;
    background: var(--gold);
  }
  .identity__name {
    font-family: "Libre Baskerville", serif;
    font-weight: 700;
    font-size: 19px;
    color: var(--gold);
    text-transform: uppercase;
    letter-spacing: 0.01em;
  }
  .identity__title {
    margin-top: 4px;
    font-size: 12px;
    line-height: 1.35;
  }
  .address {
    position: absolute;
    left: 74px; top: 146px;
    font-size: 12px;
    font-style: normal;
    line-height: 1.45;
  }
  .contact {
    position: absolute;
    left: 74px; top: 200px;
    list-style: none;
    font-size: 12px;
    line-height: 1.55;
    z-index: 2;
  }
  .contact li { display: flex; align-items: center; gap: 7px; }
  .contact svg { width: 11px; height: 11px; fill: var(--gold); flex: none; }
</style>
</head>
<body>

  <section class="card card--back" aria-label="Card back">
    <div class="brand">RV Bone<br>&amp; Vitality<br>Center</div>
    <p class="tagline">Steady Hands. Lasting Strength</p>
  </section>

  <section class="card card--front" aria-label="Card front">
    <svg class="swoosh" viewBox="0 0 540 310" aria-hidden="true">
      <path d="M150 310 Q 390 268 540 150 L540 310 Z" fill="var(--gold)"/>
      <path d="M118 300 Q 372 262 540 134" fill="none" stroke="var(--white)" stroke-width="4"/>
    </svg>

    <div class="brand">RV Bone<br>&amp; Vitality<br>Center</div>

    <div class="identity">
      <h1 class="identity__name">Lydia Vance, M.D.</h1>
      <p class="identity__title">Board Certified Hand and Upper<br>Extremity Surgeon</p>
    </div>

    <address class="address">
      38517 North Willowmere Ave<br>Palm Haven, FL 33490
    </address>

    <ul class="contact">
      <li>
        <svg viewBox="0 0 24 24" aria-hidden="true"><path d="M6.6 10.8a15.1 15.1 0 0 0 6.6 6.6l2.2-2.2a1 1 0 0 1 1-.25 11.4 11.4 0 0 0 3.6.57 1 1 0 0 1 1 1V20a1 1 0 0 1-1 1A17 17 0 0 1 3 4a1 1 0 0 1 1-1h3.5a1 1 0 0 1 1 1c0 1.25.2 2.45.57 3.570a1 1 0 0 1-.25 1z"/></svg>
        954-218-4063
      </li>
      <li>
        <svg viewBox="0 0 24 24" aria-hidden="true"><path d="M6 2h12v6H6zM4 9h16a2 2 0 0 1 2 2v6h-4v5H6v-5H2v-6a2 2 0 0 1 2-2zm4 8v3h8v-3z"/></svg>
        954-582-7341
      </li>
      <li>
        <svg viewBox="0 0 24 24" aria-hidden="true"><path d="M2 5h20v14H2zm2 2v.5l8 5 8-5V7l-8 5z"/></svg>
        info@myrvbonecare.example
      </li>
    </ul>
  </section>

</body>
</html>
```